Velvet Lantern rebranding my business with a new business card

I have my new logo and now I need a refresher on my business cards. I really want something fun and fresh. I like black background or anything to make the color pop.
Logo
Name: Velvet Lantern
Contact Info as stated below:
Mira Pellow
555-013-4762
Logo
Name: Velvet Lantern
Mira Pellow
555-013-4762
fb.me/VelvetLanternbyMira
Instagram: @VelvetLanternbyMira

Industry/Entity Type

Business

Contact Information for Business Card

double-sided. Logo on one side. Contact info on the other.

Requirements
Must have
• Logo
• Name: Velvet Lantern
• Contact Info as stated below:
• Mira Pellow
• 555-013-4762
• fb.me/VelvetLanternbyMira
• fb.me/VelvetLanternbyMira

```html
<!DOCTYPE html>
<html lang="en">
<head>
<meta charset="utf-8">
<title>Velvet Lantern – Business Card</title>
<link rel="stylesheet" href="https://fonts.googleapis.com/css2?family=Comic+Neue:wght@400;700&display=swap">
<style>
  :root {
    --backdrop: #4d4d4d;
    --card-front: #f7bfc1;
    --card-back: #f8f8f8;
    --ink: #111111;
    --ring-pink: #f29bb0;
    --white: #ffffff;
  }
  html, body {
    margin: 0;
    padding: 0;
    overflow: hidden;
  }
  body {
    width: 1200px;
    height: 849px;
    background: var(--backdrop);
    position: relative;
    font-family: "Comic Neue", "Comic Sans MS", cursive;
    color: var(--ink);
  }
  .card {
    position: absolute;
  }
  .card-front {
    left: 162px;
    top: 274px;
    width: 498px;
    height: 300px;
    background: var(--card-front);
  }
  .card-back {
    left: 700px;
    top: 176px;
    width: 300px;
    height: 497px;
    background: var(--card-back);
  }
  .logo-badge {
    position: absolute;
    width: 198px;
    height: 198px;
  }
  .card-front .logo-badge { left: 149px; top: 51px; }
  .card-back .logo-badge { left: 51px; top: 54px; }
  .logo-badge svg { display: block; }
  .brand-name {
    font-family: "Comic Neue", "Comic Sans MS", cursive;
    font-weight: 700;
    font-size: 24px;
    fill: var(--ink);
  }
  .person-name {
    position: absolute;
    top: 288px;
    left: 0;
    width: 100%;
    text-align: center;
    font-size: 30px;
    font-weight: 400;
    letter-spacing: 0.5px;
  }
  .contact-divider {
    position: absolute;
    left: 0;
    width: 100%;
    display: flex;
    justify-content: center;
  }
  .contact-divider.phone { top: 346px; }
  .contact-divider.social { top: 400px; }
  .contact-line {
    position: absolute;
    left: 0;
    width: 100%;
    text-align: center;
    font-size: 17px;
    font-weight: 400;
  }
  .contact-line.phone { top: 373px; }
  .contact-line.social { top: 424px; }
</style>
</head>
<body>

  <section class="card card-front" aria-label="Business card front">
    <div class="logo-badge">
      <svg width="198" height="198" viewBox="0 0 198 198">
        <circle cx="99" cy="99" r="97" fill="var(--white)" stroke="var(--ink)" stroke-width="2"/>
        <circle cx="99" cy="99" r="91" fill="none" stroke="var(--ring-pink)" stroke-width="1.2"/>
        <circle cx="99" cy="99" r="88" fill="none" stroke="var(--ring-pink)" stroke-width="0.8"/>
        <text class="brand-name" x="99" y="95" text-anchor="middle">Velvet</text>
        <text class="brand-name" x="99" y="122" text-anchor="middle">Lantern</text>
      </svg>
    </div>
  </section>

  <section class="card card-back" aria-label="Business card back">
    <div class="logo-badge">
      <svg width="198" height="198" viewBox="0 0 198 198">
        <circle cx="99" cy="99" r="97" fill="var(--white)" stroke="var(--ink)" stroke-width="2"/>
        <circle cx="99" cy="99" r="91" fill="none" stroke="var(--ring-pink)" stroke-width="1.2"/>
        <circle cx="99" cy="99" r="88" fill="none" stroke="var(--ring-pink)" stroke-width="0.8"/>
        <text class="brand-name" x="99" y="95" text-anchor="middle">Velvet</text>
        <text class="brand-name" x="99" y="122" text-anchor="middle">Lantern</text>
      </svg>
    </div>

    <div class="person-name">Mira Pellow</div>

    <div class="contact-divider phone">
      <svg width="124" height="22" viewBox="0 0 124 22">
        <path d="M2 12 Q14 9 26 11 T42 10" fill="none" stroke="var(--ink)" stroke-width="1"/>
        <path d="M82 10 Q94 9 106 11 T122 12" fill="none" stroke="var(--ink)" stroke-width="1"/>
        <rect x="52" y="1" width="20" height="20" rx="4" fill="var(--white)" stroke="var(--ink)" stroke-width="1.4"/>
        <path d="M57.5 6.5 l2.5 -1 l1.8 3 l-1.5 1.2 q1 2.3 3 3.3 l1.2 -1.5 l3 1.8 l-1 2.5 q-6 0.5 -9 -9.3z" fill="var(--ink)"/>
      </svg>
    </div>
    <div class="contact-line phone">555-013-4762</div>

    <div class="contact-divider social">
      <svg width="124" height="22" viewBox="0 0 124 22">
        <path d="M2 12 Q14 9 26 11 T42 10" fill="none" stroke="var(--ink)" stroke-width="1"/>
        <path d="M82 10 Q94 9 106 11 T122 12" fill="none" stroke="var(--ink)" stroke-width="1"/>
        <rect x="52" y="1" width="20" height="20" rx="4" fill="var(--white)" stroke="var(--ink)" stroke-width="1.4"/>
      </svg>
    </div>
    <div class="contact-line social">VelvetLanternbyMira</div>
  </section>

</body>
</html>
```